Business Cards - New Logo Rebranding

Hello We know have a red and blue logo and are looking to create new cards. We are looking for the best creativity of the new logo merged with some of the existing artwork provided.

Target Market(s)

Realtors

Industry/Entity Type

Real Estate

Contact Information for Business Card

New logo with rebranded colors

Requirements
Must have
• Creative use of the new logo

```html
<!DOCTYPE html>
<html lang="en">
<head>
<meta charset="utf-8">
<title>Summit Crest – Business Card</title>
<link href="https://fonts.googleapis.com/css2?family=Figtree:wght@400;500;600;700;800&display=swap" rel="stylesheet">
<style>
  :root {
    --brand-blue: #0b6fbb;
    --brand-blue-deep: #0a5fa3;
    --brand-red: #e0313c;
    --card-white: #f3f3f4;
    --ink: #2b2b2b;
    --page: #e2e2e2;
    --white: #ffffff;
  }
  * { box-sizing: border-box; margin: 0; padding: 0; }
  html, body {
    width: 1200px; height: 1059px; overflow: hidden;
    background: var(--page);
    font-family: "Figtree", sans-serif;
  }
  .card {
    position: absolute; left: 255px; width: 690px; height: 392px;
    border-radius: 22px; overflow: hidden;
  }
  /* ---------- front ---------- */
  .card--front { top: 100px; background: var(--card-white); }
  .edge-band { position: absolute; left: 0; top: 0; bottom: 0; width: 20px; background: var(--brand-blue); }
  .edge-rule { position: absolute; left: 23px; top: 0; bottom: 0; width: 3px; background: var(--brand-red); }

  .brand-mark { position: absolute; left: 109px; top: 36px; width: 80px; height: 80px; border-radius: 50%; background: var(--brand-blue); }
  .brand-name {
    position: absolute; left: 47px; top: 116px; width: 206px; text-align: center;
    font-weight: 800; font-size: 25px; letter-spacing: 0.5px; color: var(--brand-blue);
  }
  .brand-tagline {
    position: absolute; left: 47px; top: 146px; width: 206px;
    display: flex; align-items: center; gap: 4px;
    font-size: 8px; font-weight: 600; color: var(--brand-blue); white-space: nowrap;
  }
  .brand-tagline::before, .brand-tagline::after { content: ""; flex: 1; height: 1.5px; background: var(--brand-blue); }

  .person-name { position: absolute; left: 47px; top: 183px; font-size: 26px; font-weight: 800; color: var(--brand-blue); }
  .person-name .surname { color: var(--brand-red); }
  .person-title { position: absolute; left: 47px; top: 212px; font-size: 16px; color: var(--ink); }

  .portrait {
    position: absolute; left: 459px; top: 24px; width: 201px; height: 223px;
    background: linear-gradient(180deg, #d9d4cf 0%, #b89c86 38%, #1f5db0 62%, #1a4f9c 100%);
    border-radius: 90px 90px 0 0;
  }
  .divider { position: absolute; left: 47px; top: 246px; width: 613px; height: 1.5px; background: var(--brand-red); }

  .contact-list { position: absolute; left: 47px; top: 259px; list-style: none; }
  .contact-list li { display: flex; align-items: center; height: 26.5px; font-size: 17px; color: var(--ink); }
  .contact-list svg { width: 16px; height: 16px; margin-right: 8px; fill: var(--brand-blue); flex: none; }

  .services { position: absolute; left: 430px; top: 311px; list-style: none; font-size: 17px; color: var(--ink); }
  .services li { height: 26.5px; display: flex; align-items: center; }
  .services .dot { color: var(--brand-red); margin: 0 5px 0 0; }
  .services .dot + .dot, .services span + .dot { margin-left: 5px; }

  /* ---------- back ---------- */
  .card--back { top: 537px; background: var(--brand-blue); }
  .back-headline {
    position: absolute; top: 36px; left: 0; right: 0; text-align: center;
    font-size: 28px; font-weight: 800; color: var(--white); letter-spacing: 0.2px;
  }
  .back-rule { position: absolute; left: 0; right: 0; top: 111px; height: 2px; background: var(--brand-red); }
  .back-pill {
    position: absolute; left: 170px; top: 94px; width: 353px; height: 37px; border-radius: 19px;
    background: var(--brand-red); color: var(--white);
    display: flex; align-items: center; justify-content: center;
    font-size: 23px; font-weight: 500;
  }
  .reasons { position: absolute; top: 156px; list-style: none; color: var(--white); font-size: 17.5px; font-weight: 600; line-height: 23px; }
  .reasons--left { left: 42px; width: 320px; }
  .reasons--right { left: 384px; width: 300px; }
  .reasons li { position: relative; margin-bottom: 7px; }
  .reasons li::before { content: ""; position: absolute; left: -11px; top: 10px; width: 4px; height: 4px; border-radius: 50%; background: var(--brand-red); }
  .reasons--right li { margin-bottom: 10px; }

  .credentials { position: absolute; left: 0; top: 0; width: 690px; height: 392px; pointer-events: none; }
</style>
</head>
<body>

<section class="card card--front" aria-label="Business card front">
  <div class="edge-band"></div>
  <div class="edge-rule"></div>

  <div class="brand-mark"></div>
  <div class="brand-name">SUMMIT CREST</div>
  <div class="brand-tagline">INSPECTION PROFESSIONALS</div>

  <h1 class="person-name">DAN <span class="surname">MARLOW</span></h1>
  <p class="person-title">Certified Mold Inspector</p>

  <div class="portrait" role="img" aria-label="Portrait photo of the inspector in a blue company polo shirt"></div>
  <div class="divider"></div>

  <ul class="contact-list">
    <li><svg viewBox="0 0 24 24"><path d="M6.6 10.8a15.1 15.1 0 0 0 6.6 6.6l2.2-2.2a1 1 0 0 1 1-.25 11.4 11.4 0 0 0 3.6.57 1 1 0 0 1 1 1V20a1 1 0 0 1-1 1A17 17 0 0 1 3 4a1 1 0 0 1 1-1h3.5a1 1 0 0 1 1 1c0 1.25.2 2.45.57 3.57a1 1 0 0 1-.25 1z"/></svg>800.555.0142</li>
    <li><svg viewBox="0 0 24 24"><path d="M7 1h10a2 2 0 0 1 2 2v18a2 2 0 0 1-2 2H7a2 2 0 0 1-2-2V3a2 2 0 0 1 2-2zm0 3v14h10V4zm5 15.5a1.2 1.2 0 1 0 0 2.4 1.2 1.2 0 0 0 0-2.4z"/></svg>562.555.0187</li>
    <li><svg viewBox="0 0 24 24"><path d="M2 5h20v14H2zm2 2v.4l8 5.6 8-5.6V7zm0 2.8V17h16V9.8l-8 5.6z"/></svg>danmarlow@summitcrestinspect.com</li>
    <li><svg viewBox="0 0 24 24"><path d="M12 2a10 10 0 1 0 0 20 10 10 0 0 0 0-20zm6.9 6h-3a15.7 15.7 0 0 0-1.4-3.6A8 8 0 0 1 18.9 8zM12 4a14 14 0 0 1 1.9 4h-3.8A14 14 0 0 1 12 4zM4.3 14a8 8 0 0 1 0-4h3.4a16.5 16.5 0 0 0 0 4zm.8 2h3a15.7 15.7 0 0 0 1.4 3.6A8 8 0 0 1 5.1 16zm3-8h-3a8 8 0 0 1 4.4-3.6A15.7 15.7 0 0 0 8.1 8zM12 20a14 14 0 0 1-1.9-4h3.8A14 14 0 0 1 12 20zm2.3-6H9.7a14.7 14.7 0 0 1 0-4h4.6a14.7 14.7 0 0 1 0 4zm.2 5.6a15.7 15.7 0 0 0 1.4-3.6h3a8 8 0 0 1-4.4 3.6zm1.8-5.6a16.5 16.5 0 0 0 0-4h3.4a8 8 0 0 1 0 4z"/></svg>www.SummitCrestInspect.com</li>
  </ul>

  <ul class="services">
    <li><span class="dot">•</span>Home<span class="dot">•</span>Sewer<span class="dot">•</span>Mold<span class="dot">•</span>Roof</li>
    <li><span class="dot">•</span>Commercial<span class="dot">•</span>Termite</li>
  </ul>
</section>

<section class="card card--back" aria-label="Business card back">
  <h2 class="back-headline">CALIFORNIA’S #1 INSPECTION COMPANY!</h2>
  <div class="back-rule"></div>
  <div class="back-pill">Why Choose Summit Crest</div>

  <ul class="reasons reasons--left">
    <li>Performing Inspections Since 1984</li>
    <li>NorthStar Certified Master / Professional Inspectors®</li>
    <li>500,000+ Inspections Completed Statewide</li>
    <li>90-Day Inspection Guarantees</li>
  </ul>
  <ul class="reasons reasons--right">
    <li>Request of Repairs Pricer Report</li>
    <li>SkyCert Drone Licensed Roof Inspectors upon request</li>
    <li>5,000+ 5-Star Reviews on ReviewHub &amp; LocalStar</li>
  </ul>

  <svg class="credentials" viewBox="0 0 690 392" aria-label="Certification and review badges">
    <circle cx="357" cy="354" r="18" fill="#f3f3f4" stroke="#e0313c" stroke-width="3"/>
    <circle cx="410" cy="354" r="18" fill="#c9a227" stroke="#e8d27a" stroke-width="2"/>
    <circle cx="462" cy="354" r="18" fill="#cfc7b0" stroke="#f3f3f4" stroke-width="2"/>
    <rect x="495.5" y="336" width="2" height="36" fill="#e0313c"/>
    <rect x="514" y="344" width="63" height="21" fill="#1f2f6b" stroke="#c9a227" stroke-width="1.5"/>
    <rect x="590" y="342" width="44" height="24" rx="3" fill="#f3f3f4"/>
    <circle cx="657" cy="354" r="11" fill="#f3f3f4"/>
  </svg>
</section>

</body>
</html>
```